Stylish Business Cards Wanted

- DOUBLE SIDED Design Required -

High end, edgy cards for a corporate and personal stylist. Must include logo,
Name: Belinda Harwick
Title: Director and Stylist
telephone : +61 8 7142 5809
email: belinda@theloombriefing.example
website: theloombriefing.example
Tag: Corporate Workwear & Uniform Specialist | Personal Stylist
Would like nice icons for telephone, email, website

Target Market(s)

Businesses wanting stylish uniforms, people wanting stylish wardrobes

Industry/Entity Type

Corporate Workwear Stylist

Contact Information for Business Card

I would like black, white and gold foiling incorporated in the design - possibly a touch of the other colours on my branding guide attached Name: Belinda Harwick Title: Director and Stylist telephone : +61 8 7142 5809 email: belinda@theloombriefing.example website: theloombriefing.example Tag: Corporate Workwear & Uniform Specialist | Personal Stylist Would like nice icons for telephone, email, website

Font styles to use
Other font styles liked:
• Raleway

Colors

Designer to choose colors to be used in the design.

Requirements
Must have
• Gold foil accents

```html
<!DOCTYPE html>
<html lang="en">
<head>
<meta charset="utf-8">
<title>The Loom Briefing — Business Cards</title>
<link rel="stylesheet" href="https://fonts.googleapis.com/css2?family=Raleway:wght@400;500;600;700&display=swap">
<style>
  :root {
    --bg: #e9e7e3;
    --card-black: #1b1c1c;
    --gloss-black: #2e3030;
    --paper: #f7f9f8;
    --ink: #111111;
    --gold: #e0a92a;
    --band: #0d0d0d;
    --band-text: #ffffff;
  }
  * { margin: 0; padding: 0; box-sizing: border-box; }
  html, body {
    width: 1200px; height: 863px; overflow: hidden;
    background: var(--bg);
    font-family: "Raleway", sans-serif;
  }
  .sheet {
    width: 1200px; height: 863px;
    display: flex; align-items: center; justify-content: center; gap: 60px;
  }
  .card {
    width: 525px; height: 300px;
    border-radius: 22px;
    position: relative;
    overflow: hidden;
    box-shadow: 0 10px 26px rgba(0,0,0,.18);
  }

  /* Back */
  .card--back { background: var(--card-black); display: flex; align-items: center; justify-content: center; }
  .wordmark { display: flex; align-items: center; gap: 12px; font-weight: 700; letter-spacing: .04em; }
  .wordmark__square { width: 14px; height: 14px; background: var(--gold); }
  .card--back .wordmark__name { color: var(--gloss-black); font-size: 40px; }

  /* Front */
  .card--front { background: var(--paper); }
  .front__body {
    position: absolute; left: 0; right: 0; top: 0; bottom: 58px;
    display: flex; align-items: center; padding: 0 34px 0 40px; gap: 34px;
  }
  .card--front .wordmark { flex-direction: column; align-items: flex-start; gap: 8px; }
  .card--front .wordmark__name { color: var(--ink); font-size: 28px; line-height: 1.05; }
  .contact__name { font-size: 25px; font-weight: 700; color: var(--ink); line-height: 1.1; }
  .contact__title { font-size: 12px; color: var(--gold); font-weight: 500; margin: 2px 0 12px; }
  .contact__list { list-style: none; }
  .contact__item { display: flex; align-items: center; gap: 9px; font-size: 12.5px; color: var(--ink); margin-bottom: 6px; }
  .contact__item svg { width: 12px; height: 12px; flex: none; }
  .front__band {
    position: absolute; left: 0; right: 0; bottom: 0; height: 58px;
    background: var(--band); color: var(--band-text);
    display: flex; align-items: center; justify-content: center;
    font-size: 15px; font-weight: 500; letter-spacing: .01em;
  }
</style>
</head>
<body>
<main class="sheet">
  <section class="card card--back" aria-label="Card back">
    <div class="wordmark">
      <span class="wordmark__square"></span>
      <span class="wordmark__name">The Loom Briefing</span>
    </div>
  </section>

  <section class="card card--front" aria-label="Card front">
    <div class="front__body">
      <div class="wordmark">
        <span class="wordmark__square"></span>
        <span class="wordmark__name">The Loom<br>Briefing</span>
      </div>
      <div class="contact">
        <h1 class="contact__name">Belinda Harwick</h1>
        <p class="contact__title">Director and Stylist</p>
        <ul class="contact__list">
          <li class="contact__item">
            <svg viewBox="0 0 24 24" aria-hidden="true"><path fill="#111" d="M6.6 10.8a15.1 15.1 0 0 0 6.6 6.6l2.2-2.2c.3-.3.7-.4 1-.2 1.1.4 2.3.6 3.6.6.6 0 1 .4 1 1V20c0 .6-.4 1-1 1A17 17 0 0 1 3 4c0-.6.4-1 1-1h3.5c.6 0 1 .4 1 1 0 1.3.2 2.5.6 3.6.1.3 0 .7-.2 1z"/></svg>
            +61 8 7142 5809
          </li>
          <li class="contact__item">
            <svg viewBox="0 0 24 24" aria-hidden="true"><path fill="#111" d="M2 5h20v14H2z"/><path fill="none" stroke="#f7f9f8" stroke-width="1.8" d="M2.5 5.5 12 13l9.5-7.5"/></svg>
            belinda@theloombriefing.example
          </li>
          <li class="contact__item">
            <svg viewBox="0 0 24 24" aria-hidden="true"><circle cx="12" cy="12" r="10" fill="#111"/><path fill="none" stroke="#f7f9f8" stroke-width="1.4" d="M2 12h20M12 2c3 3 3 17 0 20M12 2c-3 3-3 17 0 20"/></svg>
            www.theloombriefing.example
          </li>
        </ul>
      </div>
    </div>
    <p class="front__band">Corporate Workwear &amp; Uniform Specialist | Personal Stylist</p>
  </section>
</main>
</body>
</html>
```